Crestline Staffing PEO - Web Build for Professional Employment Organization

We need a website built for our new PEO (professional employment organization). This company will offer third party Human Resource services to companies who are looking to outsource:<br/>Recruiting<br/>Administrative Onboarding<br/>New hire training, ongoing training and development<br/>Payroll/compensation processing/services<br/>Employee Relations<br/>Unemployment Claim Facilitation<br/>Benefits Plans and Administration<br/><br/>I have attached the logo below. Please use that as a reference and color match as best as possible. <br/><br/>Here are some of the competitor's websites:<br/>https://www.velmorahr.com/ <br/>https://www.trundelpay.com/<br/>https://www.trundelpay.com/<br/>https://www.qzn.com/<br/>https://www.bremwickhr.com/<br/>https://orvalepeo.com/contact-orvale/<br/><br/>

Target Market(s)

Startups and mid-sized businesses

Number of Pages Required

5+ page

Font styles to use
Sans Serif

Colors
0592cd

Requirements
Must have
• Features Pages
• SEO driven keyword rich content
• Strong focus on our ability to provide unemployment claim facilitation services as well as mandatory training/certification fulfillment
Nice to have
• I'd like to see one mockup with a Live Chat version if possible. In theory, the Live Chat messages would go directly to our front desk person.

```html
<!DOCTYPE html>
<html lang="en">
<head>
<meta charset="utf-8">
<title>Crestline Staffing PEO – Professional Employment Organization</title>
<link href="https://fonts.googleapis.com/css2?family=Raleway:wght@400;500;600&family=Roboto:wght@500;700;900&display=swap" rel="stylesheet">
<style>
:root{
  --blue:#0592cd;
  --blue-dark:#0a79ad;
  --navy:#3d4d6a;
  --ink:#1a1a1a;
  --text:#333;
  --muted:#777;
  --white:#fff;
  --black:#000;
  --card-shadow:0 6px 18px rgba(0,0,0,.08);
}
*{box-sizing:border-box;margin:0;padding:0}
html,body{width:1200px;height:4107px;overflow:hidden}
body{font-family:"Raleway",sans-serif;color:var(--text);background:var(--white);position:relative}
.abs{position:absolute}
.topbar{top:0;left:0;width:1200px;height:45px;background:var(--navy);color:#fff;font-size:16px}
.topbar .social{left:89px;top:16px;display:flex;gap:20px}
.dot-icon{width:12px;height:12px;border-radius:50%;background:#fff;display:block}
.topbar .login{left:628px;top:0;width:125px;height:45px;display:flex;align-items:center;justify-content:center;gap:8px;border-left:1px solid #566684;border-right:1px solid #566684}
.topbar .lang{left:753px;top:0;width:160px;height:45px;display:flex;align-items:center;justify-content:center;gap:8px}
.topbar .quote{left:914px;top:0;width:197px;height:45px;background:var(--blue);display:flex;align-items:center;justify-content:center;font-weight:600;font-size:18px}
.nav{top:45px;left:0;width:1200px;height:93px;background:#fff}
.brand{left:89px;top:18px;font-family:"Roboto",sans-serif;font-weight:700;font-size:30px;color:var(--navy);display:flex;align-items:center;gap:10px;line-height:1}
.brand .mark{width:16px;height:16px;border-radius:50%;background:var(--blue)}
.brand small{display:block;font-size:16px;color:var(--blue);letter-spacing:6px;margin-top:6px;font-weight:500}
.menu{right:89px;top:38px;display:flex;gap:44px;font-size:17px;color:#333}
.menu .active{color:var(--blue)}
.hero{top:138px;left:0;width:1200px;height:683px;background:linear-gradient(180deg,#9aa6b3 0%,#6c7b8c 55%,#4c5a6b 100%);clip-path:polygon(0 0,100% 0,100% 563px,50% 683px,0 563px)}
.hero h1{position:absolute;top:165px;width:100%;text-align:center;font-family:"Roboto",sans-serif;font-weight:900;font-size:80px;color:#fff;line-height:1}
.hero p{position:absolute;top:248px;width:100%;text-align:center;font-size:40px;color:#fff;letter-spacing:1px}
.hero .btn{position:absolute;left:465px;top:353px;width:270px;height:56px;background:var(--blue);color:#fff;font-size:20px;font-weight:600;display:flex;align-items:center;justify-content:center}
.hero-dots{position:absolute;left:567px;top:558px;display:flex;gap:6px}
.hero-dots i{width:12px;height:12px;border-radius:50%;background:#fff}
.hero-dots i:first-child{background:var(--blue)}
.hero-band{left:0;top:700px}
.sec-title{width:1200px;text-align:center;font-family:"Roboto",sans-serif;font-weight:700;font-size:36px;color:var(--ink);text-transform:uppercase}
.sec-title span{color:var(--blue)}
.rule{width:40px;height:5px;background:var(--blue)}
.card{width:242px;height:229px;background:#fff;box-shadow:var(--card-shadow);text-align:center;font-size:18px;line-height:27px;color:#222}
.card svg{display:block;margin:48px auto 22px}
.stats{top:1685px;left:0;width:1200px;height:486px;background:linear-gradient(180deg,#2f88bd,#0a8fcf)}
.stats h2{position:absolute;top:70px;width:100%;text-align:center;font-family:"Roboto",sans-serif;font-weight:700;font-size:36px;line-height:44px;color:#fff}
.stat{width:260px;text-align:center;color:#fff}
.stat b{display:block;font-family:"Roboto",sans-serif;font-weight:900;font-size:40px}
.stat strong{display:block;font-size:24px;font-weight:600;margin-top:16px}
.stat p{font-size:16px;line-height:24px;margin-top:8px}
.divider{width:1px;height:200px;background:rgba(255,255,255,.35);top:210px}
.quote-side{top:2427px;width:310px;height:213px;background:#f7f7f7;color:#ccc;font-size:12px;line-height:20px;text-align:center;padding:36px 34px}
.quote-main{top:2396px;left:351px;width:499px;height:276px;background:var(--blue);color:#fff;font-size:17px;line-height:28px;text-align:center;padding:32px 60px}
.qmark{font-family:"Roboto",sans-serif;font-size:50px;line-height:1;position:absolute;font-weight:900}
.avatar{border-radius:50%;background:linear-gradient(#c9ced4,#8e959d)}
.who-photo{top:2901px;left:0;width:600px;height:542px;background:linear-gradient(135deg,#d8d4cd,#a59c90 60%,#7c8891)}
.who{top:2901px;left:600px;width:600px;height:542px;background:var(--blue);color:#fff}
.who h2{position:absolute;left:85px;top:72px;font-family:"Roboto",sans-serif;font-weight:700;font-size:36px}
.who .rule{background:#fff;position:absolute;left:85px;top:130px}
.who p{position:absolute;left:85px;top:152px;width:426px;font-size:17px;line-height:34px;text-align:justify}
.who .btn{position:absolute;left:85px;top:417px;width:160px;height:47px;border:2px solid #fff;display:flex;align-items:center;justify-content:center;font-size:18px;font-weight:600}
.clients{top:3550px;left:0;width:1200px;display:flex;justify-content:space-around;padding:0 90px;color:#8a8a8a;font-size:18px;font-weight:600}
.clients span{display:flex;align-items:center;gap:8px}
.clients span i{width:14px;height:14px;border-radius:50%;background:#9a9a9a}
.footer{top:3660px;left:0;width:1200px;height:447px}
.fcol{top:190px;font-size:15px;line-height:32px;color:#fff}
.fcol h4{font-weight:500;font-size:18px;margin-bottom:12px;letter-spacing:1px}
.fsocial{display:flex;gap:22px;margin-top:10px}
.copyright{top:4070px;width:1200px;text-align:center;color:#fff;font-size:13px}
.livechat{left:8px;top:4032px;width:95px;height:58px;border-radius:50%;background:var(--blue);color:#fff;font-size:13px;font-weight:600;line-height:16px;text-align:center;padding-top:13px}
</style>
</head>
<body>

<header>
  <div class="abs topbar">
    <div class="abs social"><i class="dot-icon"></i><i class="dot-icon"></i><i class="dot-icon"></i><i class="dot-icon"></i><i class="dot-icon"></i><i class="dot-icon"></i></div>
    <div class="abs login">
      <svg width="12" height="14" viewBox="0 0 12 14"><rect x="1" y="6" width="10" height="8" fill="#fff"/><path d="M3 6V4a3 3 0 0 1 6 0v2" stroke="#fff" stroke-width="2" fill="none"/></svg>
      Login</div>
    <div class="abs lang"><i class="dot-icon" style="width:18px;height:18px"></i>English
      <svg width="10" height="6" viewBox="0 0 10 6"><path d="M1 1l4 4 4-4" stroke="#fff" fill="none" stroke-width="1.5"/></svg></div>
    <div class="abs quote">Get a Quote</div>
  </div>
  <nav class="abs nav">
    <div class="abs brand"><span class="mark"></span><div>CRESTLINE STAFFING<small>PEO</small></div></div>
    <div class="abs menu"><span class="active">Home</span><span>Abolut Us</span><span>Services</span><span>Solution</span><span>Careers</span><span>Contact us</span></div>
  </nav>
</header>

<section class="abs hero" role="img" aria-label="Business people in silhouette over a city skyline">
  <h1>CRESTLINE STAFFING</h1>
  <p>Professional Employment Organization</p>
  <div class="btn">Explore HR Solutions</div>
  <div class="hero-dots"><i></i><i></i><i></i><i></i></div>
</section>
<svg class="abs hero-band" width="1200" height="150" viewBox="0 0 1200 150">
  <path d="M95 33 L600 126 L1105 33 L600 145Z" fill="var(--blue)"/>
</svg>

<section>
  <h2 class="abs sec-title" style="top:965px">Our full-service <span>HR solution delivers</span></h2>
  <div class="abs rule" style="left:580px;top:1027px"></div>

  <div class="abs card" style="left:89px;top:1073px">
    <svg width="60" height="60" viewBox="0 0 60 60" fill="none" stroke="var(--blue)" stroke-width="2"><circle cx="26" cy="24" r="16"/><circle cx="26" cy="20" r="5"/><path d="M17 33c3-6 15-6 18 0M38 36l14 14"/><path d="M44 8h10M44 14h8M44 20h10"/></svg>
    Recruiting</div>
  <div class="abs card" style="left:349px;top:1073px">
    <svg width="60" height="60" viewBox="0 0 60 60" fill="none" stroke="var(--blue)" stroke-width="2"><circle cx="24" cy="22" r="8"/><path d="M10 56c0-14 28-14 28 0"/><rect x="36" y="6" width="18" height="14" rx="2"/><path d="M40 11h10M40 15h6"/></svg>
    Administrative<br>Onboarding</div>
  <div class="abs card" style="left:609px;top:1073px">
    <svg width="60" height="60" viewBox="0 0 60 60" fill="none" stroke="var(--blue)" stroke-width="2"><rect x="10" y="6" width="40" height="28"/><path d="M16 28l8-8 6 5 12-12"/><circle cx="16" cy="42" r="4"/><circle cx="30" cy="42" r="4"/><circle cx="44" cy="42" r="4"/><path d="M9 56c0-6 14-6 14 0M23 56c0-6 14-6 14 0M37 56c0-6 14-6 14 0"/></svg>
    New hire training,<br>ongoing training and<br>development</div>
  <div class="abs card" style="left:869px;top:1073px">
    <svg width="60" height="60" viewBox="0 0 60 60" fill="none" stroke="var(--blue)" stroke-width="2"><rect x="8" y="8" width="46" height="32" rx="3"/><path d="M14 16h34M14 22h20"/><circle cx="20" cy="44" r="10"/><path d="M20 38v12"/></svg>
    Payroll/<br>compensation<br>processing/services</div>

  <div class="abs card" style="left:220px;top:1323px">
    <svg width="60" height="60" viewBox="0 0 60 60" fill="none" stroke="var(--blue)" stroke-width="2"><circle cx="30" cy="12" r="5"/><circle cx="12" cy="42" r="5"/><circle cx="48" cy="42" r="5"/><path d="M22 22c0-5 16-5 16 0M4 54c0-5 16-5 16 0M40 54c0-5 16-5 16 0M18 14a20 20 0 0 0-10 18M42 14a20 20 0 0 1 10 18M22 52h16"/></svg>
    Employee<br>Relations</div>
  <div class="abs card" style="left:480px;top:1323px">
    <svg width="60" height="60" viewBox="0 0 60 60" fill="none" stroke="var(--blue)" stroke-width="2"><rect x="10" y="6" width="34" height="48"/><circle cx="27" cy="20" r="5"/><path d="M18 34c0-7 18-7 18 0M16 42h22M16 48h16M48 14l6 4-16 26-6 2 0-6z"/></svg>
    Unemployment<br>Claim Facilitation</div>
  <div class="abs card" style="left:738px;top:1323px">
    <svg width="60" height="60" viewBox="0 0 60 60" fill="none" stroke="var(--blue)" stroke-width="2"><circle cx="22" cy="22" r="16"/><path d="M14 14l16 16M30 14L14 30"/><path d="M34 56V44M42 56V38M50 56V32M34 40l10-10 8 4"/></svg>
    Benefits Plans<br>&amp; Administration</div>
</section>

<section class="abs stats" role="img" aria-label="Job candidates seated in a row, tinted blue">
  <h2>WE ARE A HR SOLUTIONS THAT GROW<br>WITH YOUR BUSINESS</h2>
  <div class="abs rule" style="left:580px;top:178px;background:#fff"></div>
  <div class="abs stat" style="left:48px;top:230px"><b>15K+</b><strong>Employees</strong><p>Lorem ipsum dolor sit<br>amet, consectetur</p></div>
  <div class="abs stat" style="left:329px;top:230px"><b>14K+</b><strong>Solutions</strong><p>Lorem ipsum dolor sit<br>amet, consectetur</p></div>
  <div class="abs stat" style="left:611px;top:230px"><b>10K</b><strong>Employers</strong><p>Lorem ipsum dolor sit<br>amet, consectetur</p></div>
  <div class="abs stat" style="left:892px;top:230px"><b>800</b><strong>Lorem ipsum</strong><p>Lorem ipsum dolor sit<br>amet, consectetur</p></div>
  <div class="abs divider" style="left:319px"></div>
  <div class="abs divider" style="left:600px"></div>
  <div class="abs divider" style="left:883px"></div>
</section>

<section>
  <h2 class="abs sec-title" style="top:2292px">Happy <span>Employees</span></h2>
  <div class="abs rule" style="left:580px;top:2353px"></div>

  <div class="abs quote-side" style="left:59px">Sed ut perspiciatis unde omnis iste natus error sit voluptatem accusantium doloremque laudantium, totam rem aperiam, eaque ipsa quae ab illo inventore veritatis et quasi architecto</div>
  <div class="abs quote-side" style="left:831px">Sed ut perspiciatis unde omnis iste natus error sit voluptatem accusantium doloremque laudantium, totam rem aperiam, eaque ipsa quae ab illo inventore veritatis et quasi architecto</div>
  <div class="abs avatar" style="left:198px;top:2608px;width:48px;height:48px" role="img" aria-label="Employee portrait"></div>
  <div class="abs avatar" style="left:938px;top:2608px;width:48px;height:48px" role="img" aria-label="Employee portrait"></div>
  <div class="abs" style="left:152px;top:2668px;width:140px;text-align:center;font-size:9px;color:#aaa;line-height:12px">MARCUS T. ELLERY<br>Riverton</div>
  <div class="abs" style="left:892px;top:2668px;width:140px;text-align:center;font-size:9px;color:#aaa;line-height:12px">MARCUS T. ELLERY<br>Riverton</div>

  <div class="abs quote-main">
    <span class="qmark" style="left:22px;top:28px">“</span>
    Sed ut perspiciatis unde omnis iste natus error sit voluptatem accusantium doloremque laudantium, totam rem aperiam, eaque ipsa quae ab illo inventore veritatis et quasi architecto beatae vitae dicta sunt explicabo.
    <span class="qmark" style="left:360px;top:160px">”</span>
  </div>
  <div class="abs avatar" style="left:564px;top:2634px;width:74px;height:74px;border:3px solid #fff" role="img" aria-label="Portrait of Marcus T. Ellery"></div>
  <div class="abs" style="left:450px;top:2733px;width:300px;text-align:center;font-size:15px;line-height:22px;color:#333;font-weight:500">Marcus T. Ellery<br>USA</div>
</section>

<section>
  <div class="abs who-photo" role="img" aria-label="Smiling office colleagues working together at a desk"></div>
  <div class="abs who">
    <h2>WHO WE ARE</h2>
    <div class="rule"></div>
    <p>Lorem ipsum dolor sit amet, consectetur adipiscing elit, sed do eiusmod tempor incididunt ut labore et dolore magna aliqua. Ut enim ad minim veniam, quis nostrud exercitation ullamco laboris nisi ut aliquip ex ea commodo consequat. Duis aute irure dolor in rderit in voluptate velit esse cillum dolore eu fugiat nulla pariatur.</p>
    <div class="btn">Read More</div>
  </div>
</section>

<section class="abs clients">
  <span>Halvik Studio</span>
  <span><i></i>Pennmark</span>
  <span><i></i>Dovetree Solutions</span>
  <span>Brightfold</span>
  <span><i></i>Versant Co</span>
</section>

<footer class="abs footer">
  <svg class="abs" style="left:0;top:0" width="1200" height="447" viewBox="0 0 1200 447">
    <path d="M0 150 L600 10 L1200 150 V447 H0Z" fill="var(--black)"/>
    <path d="M90 122 L600 6 L1110 122 L600 22Z" fill="var(--blue)"/>
    <path d="M0 150 L600 22 L1200 150 L1200 160 L600 36 L0 160Z" fill="#fff"/>
  </svg>
  <div class="abs fcol" style="left:89px">Home<br>Abolut Us<br>Services<br>Solution<br>Careers<br>Contact us</div>
  <div class="abs fcol" style="left:332px">Faq<br>Blog<br>Sitemap<br>Impressum</div>
  <div class="abs fcol" style="left:566px;top:175px"><h4>CONTACT US</h4>Phone: 03 5550 2184<br>Linden Park, North Valewood,<br>USA<br>info@crestlinepeo.com</div>
  <div class="abs fcol" style="left:925px;top:175px"><h4>FOLLOW US</h4><div class="fsocial"><i class="dot-icon"></i><i class="dot-icon"></i><i class="dot-icon"></i><i class="dot-icon"></i><i class="dot-icon"></i><i class="dot-icon"></i></div></div>
</footer>
<div class="abs copyright">© Copyrights.2020.The Company Name.All Rights Reserved</div>
<div class="abs livechat">LIVE<br>CHAT</div>

</body>
</html>
```